Pinecroft Ridge A4 Potrait foldout brochure

We need a brochure design for this residential land development. I have attached the a style that we like to base our design on. Full colour required. will provide files required for design also. PLEASE DO NOT COPY THIS DESIGN. Come up with a new style that gives you this feeling. Please note the plan needs to be positioned landscape on the inside 2 A4 Pages.

Industry/Entity Type

Residential

Font styles to use
Other font styles liked:
• Try with Century Gothich

Requirements
Must have
• use same colours as supplied in Pinecroft ridge brochure.
Nice to have
• nice modern simple background graphics

```html
<!DOCTYPE html>
<html lang="en">
<head>
<meta charset="utf-8">
<title>Pinecroft Ridge – Brochure Cover</title>
<link rel="stylesheet" href="https://fonts.googleapis.com/css2?family=Questrial&family=Lato:wght@400;700&display=swap">
<style>
  :root {
    --stage: #d9dbdc;
    --forest: #00501f;
    --forest-deep: #003c18;
    --shade: #012a12;
    --sky: #3f8fb0;
    --navy: #1f3f6a;
    --berry: #8a3444;
    --olive: #7a8a2a;
    --leaf: #5f9e45;
    --white: #ffffff;
    --fold: rgba(0, 0, 0, 0.18);
  }
  * { box-sizing: border-box; margin: 0; padding: 0; }
  html, body {
    width: 1200px; height: 867px; overflow: hidden;
    background: var(--stage);
  }
  .spread {
    position: absolute; left: 40px; top: 38px;
    width: 1120px; height: 792px;
    display: flex;
    box-shadow: 0 2px 6px rgba(0,0,0,0.25);
  }
  .page {
    position: relative; width: 560px; height: 792px;
    background: var(--forest); overflow: hidden;
    color: var(--white);
  }
  .page--back { border-right: 1px solid var(--fold); }
  .pattern {
    position: absolute; inset: 0;
    background:
      radial-gradient(ellipse 170px 240px at 80% 16%, rgba(63,143,176,0.45), transparent 70%),
      radial-gradient(ellipse 150px 190px at 72% 40%, rgba(31,63,106,0.55), transparent 70%),
      radial-gradient(ellipse 140px 150px at 48% 56%, rgba(138,52,68,0.4), transparent 70%),
      radial-gradient(ellipse 190px 130px at 55% 80%, rgba(122,138,42,0.3), transparent 70%),
      linear-gradient(135deg, var(--forest) 0%, var(--forest-deep) 55%, var(--shade) 100%);
  }
  .brand-mark {
    position: absolute; border-radius: 50%;
    background: var(--leaf);
  }
  .page--front .brand-mark { left: 178px; top: 48px; width: 150px; height: 150px; }
  .page--back .brand-mark { left: 208px; top: 418px; width: 106px; height: 106px; }
  .brand-name {
    position: absolute; white-space: nowrap;
    font-family: "Questrial", sans-serif; font-weight: 400;
    color: var(--white); letter-spacing: -0.5px; line-height: 1;
  }
  .page--back .brand-name {
    left: 0; width: 540px; text-align: center;
    top: 538px; font-size: 44px;
  }
  .divider {
    position: absolute; left: 127px; width: 296px; top: 598px;
    height: 1px; background: rgba(255,255,255,0.75);
  }
  .contact {
    position: absolute; left: 0; width: 540px; top: 612px;
    text-align: center; font-family: "Lato", sans-serif;
    font-style: normal; font-size: 16px; line-height: 21px;
  }
  .contact .address { display: block; }
  .contact .icon { width: 13px; height: 13px; vertical-align: -1px; margin-right: 4px; fill: var(--white); }
  .contact .phone { display: block; margin-top: 8px; font-size: 20px; font-weight: 700; line-height: 24px; }
  .contact .phone .icon { width: 17px; height: 17px; vertical-align: -2px; }
  .contact .line { display: block; margin-top: 4px; }
  .page--front .brand-name {
    left: 0; width: 560px; text-align: center;
    top: 222px; font-size: 58px;
  }
  .page--front .locality {
    position: absolute; right: 76px; top: 279px;
    font-family: "Questrial", sans-serif; font-size: 12px; line-height: 1;
  }
  .web-address {
    position: absolute; left: 0; width: 560px; top: 728px;
    text-align: center; font-family: "Lato", sans-serif; font-size: 21px; line-height: 24px;
  }
  .web-address::after {
    content: ""; display: block; width: 294px; height: 1px;
    margin: 6px auto 0; background: rgba(255,255,255,0.8);
  }
</style>
</head>
<body>
  <main class="spread">
    <section class="page page--back">
      <div class="pattern" role="img" aria-label="Overlapping rounded-square outlines in green, blue, red and olive"></div>
      <div class="brand-mark"></div>
      <h2 class="brand-name">Pinecroft Ridge</h2>
      <div class="divider"></div>
      <address class="contact">
        <span class="address">
          <svg class="icon" viewBox="0 0 12 16"><path d="M6 0a6 6 0 0 0-6 6c0 4.5 6 10 6 10s6-5.5 6-10a6 6 0 0 0-6-6zm0 8.5A2.5 2.5 0 1 1 6 3.5a2.5 2.5 0 0 1 0 5z"/></svg>Pinecroft Ridge<br>
          Larchwood Lane 42b<br>
          20817 City, State
        </span>
        <span class="phone">
          <svg class="icon" viewBox="0 0 16 16"><path d="M3.5 1l2.5 3-1.5 2c1 2 3 4 5 5l2-1.5 3 2.5-1.5 3C7 15 1 9 .5 2.5z"/></svg>+01 98 7654321
        </span>
        <span class="line">
          <svg class="icon" viewBox="0 0 16 12"><path d="M0 0h16v12H0zM1.5 1.5v.5L8 7l6.5-5v-.5z"/></svg>info@pinecroftridge.com
        </span>
        <span class="line">
          <svg class="icon" viewBox="0 0 16 16"><circle cx="8" cy="8" r="7" fill="none" stroke="#fff" stroke-width="1.4"/><path d="M1 8h14M8 1c-3 3.5-3 10.5 0 14M8 1c3 3.5 3 10.5 0 14" fill="none" stroke="#fff" stroke-width="1.2"/></svg>www.pinecroftridge.com
        </span>
      </address>
    </section>
    <section class="page page--front">
      <div class="pattern" role="img" aria-label="Overlapping rounded-square outlines in green, blue, red and olive"></div>
      <div class="brand-mark"></div>
      <h1 class="brand-name">Pinecroft Ridge</h1>
      <p class="locality">Pinecroft Park</p>
      <p class="web-address">www.pinecroftridge.com</p>
    </section>
  </main>
</body>
</html>
```